New Business Card Design Project

Need a design that will create an impact / strong impression towards our clients for our business. We are in the lighting business and we do lighting retrofits for large commercial to industrial clientele.

Target Market(s)

Lighting Industry

Industry/Entity Type

Business

Font styles to use
Other font styles liked:
• we would like to use the font on our logo, not sure what it is though..

Requirements
Must have
• Our logo.
Nice to have
• We are open to suggestions that have to do with lighting.

```html
<!DOCTYPE html>
<html lang="en">
<head>
<meta charset="utf-8">
<title>Brightline Retrofit – Business Card</title>
<link href="https://fonts.googleapis.com/css2?family=Lato:wght@400;700&display=swap" rel="stylesheet">
<style>
  :root {
    --bg: #d9d4cc;
    --card: #f4f2ed;
    --green-dark: #1f7a3b;
    --green-light: #62b146;
    --text-grey: #6e6e6e;
    --divider: #9a9a9a;
  }
  html, body {
    margin: 0;
    padding: 0;
    width: 1200px;
    height: 1047px;
    overflow: hidden;
    background: var(--bg);
    font-family: "Lato", Arial, sans-serif;
  }
  .business-card {
    position: absolute;
    left: 100px;
    top: 251px;
    width: 1000px;
    height: 545px;
    background: var(--card);
    border-radius: 22px;
    overflow: hidden;
    box-shadow: 0 10px 30px rgba(0,0,0,0.15);
  }
  .side-bar {
    position: absolute;
    left: 0;
    top: 0;
    width: 52px;
    height: 100%;
    display: flex;
    flex-direction: column;
  }
  .side-bar__segment { background: var(--green-dark); }
  .side-bar__segment--top { height: 252px; }
  .side-bar__segment--middle {
    height: 84px;
    background: var(--green-light);
    border-top: 3px solid var(--card);
    border-bottom: 3px solid var(--card);
  }
  .side-bar__segment--bottom { flex: 1; }
  .brand {
    position: absolute;
    left: 91px;
    top: 70px;
    display: flex;
    align-items: center;
    gap: 14px;
  }
  .brand__mark {
    width: 34px;
    height: 34px;
    background: var(--green-dark);
  }
  .brand__name {
    font-weight: 700;
    font-size: 44px;
    color: var(--green-dark);
    letter-spacing: 1px;
  }
  .person {
    position: absolute;
    left: 91px;
    top: 268px;
  }
  .person__name {
    font-size: 28px;
    font-weight: 400;
    color: var(--green-dark);
    letter-spacing: 1px;
    margin: 0;
  }
  .person__title {
    font-size: 22px;
    color: var(--text-grey);
    margin: 2px 0 0;
  }
  .contact-list {
    position: absolute;
    left: 91px;
    top: 385px;
    list-style: none;
    margin: 0;
    padding: 0;
  }
  .contact-list__item {
    display: flex;
    align-items: center;
    height: 31px;
    font-size: 20px;
    color: var(--text-grey);
    letter-spacing: 0.5px;
  }
  .contact-list__icon {
    width: 16px;
    height: 16px;
    margin: 0 20px 0 10px;
    fill: var(--green-dark);
  }
  .contact-divider {
    position: absolute;
    left: 428px;
    top: 385px;
    width: 1px;
    height: 72px;
    background: var(--divider);
  }
  .address {
    position: absolute;
    left: 470px;
    top: 385px;
    font-style: normal;
    font-size: 21px;
    line-height: 31px;
    color: var(--text-grey);
    letter-spacing: 0.5px;
  }
  .swoosh {
    position: absolute;
    left: 0;
    top: 0;
    width: 1000px;
    height: 545px;
  }
</style>
</head>
<body>
  <div class="business-card">
    <svg class="swoosh" viewBox="0 0 1000 545" aria-hidden="true">
      <path d="M410 545 Q760 480 1000 358" fill="none" stroke="#62b146" stroke-width="5"/>
      <path d="M470 545 Q780 490 1000 380 L1000 545 Z" fill="#1f7a3b"/>
    </svg>

    <div class="side-bar">
      <div class="side-bar__segment side-bar__segment--top"></div>
      <div class="side-bar__segment side-bar__segment--middle"></div>
      <div class="side-bar__segment side-bar__segment--bottom"></div>
    </div>

    <div class="brand">
      <span class="brand__name">Brightline Retrofit</span>
      <span class="brand__mark"></span>
    </div>

    <div class="person">
      <h1 class="person__name">DANIEL REYES</h1>
      <p class="person__title">Founder</p>
    </div>

    <ul class="contact-list">
      <li class="contact-list__item">
        <svg class="contact-list__icon" viewBox="0 0 16 16"><path d="M3.5 1 L6 1 L7 4.5 L5.3 5.8 Q6.6 8.8 10.2 10.7 L11.5 9 L15 10 L15 12.5 Q14.5 15 12 15 Q2 14 1 4 Q1 1.5 3.5 1 Z"/></svg>
        0400 555 018
      </li>
      <li class="contact-list__item">
        <svg class="contact-list__icon" viewBox="0 0 16 16"><path d="M1 3 H15 V4 L8 9 L1 4 Z M1 5.5 L8 10.5 L15 5.5 V13 H1 Z"/></svg>
        info@brightlineretrofit.com
      </li>
      <li class="contact-list__item">
        <svg class="contact-list__icon" viewBox="0 0 16 16"><circle cx="8" cy="8" r="7"/><path d="M1 8 H15 M8 1 V15 M8 1 Q3 8 8 15 M8 1 Q13 8 8 15" stroke="#f4f2ed" stroke-width="1" fill="none"/></svg>
        www.brightlineretrofit.com
      </li>
    </ul>

    <div class="contact-divider"></div>

    <address class="address">
      2140 East<br>
      Maple Drive, Suite<br>
      A210 Mesa 85201
    </address>
  </div>
</body>
</html>
```